****Business Card Design for Quarrystone Development. Design based around attached logo/company name

I’m looking for business card design for my company Quarrystone Development Group,LLC. Design should be professional, sharp and minimal. Outside of the attached logos, greyscale colors for remainder of cards. My thoughts are two-sided card with attached logo on one side and my info on the other but open to one-sided as well with right design.
Target Market(s)
Real estate professionals including banks, private investors, property owners, developers, commercial tenants like Brewlantern, Grovika or Tanquist’s.
Industry/Entity Type
Commercial real estate development and investments.
Contact Information for Business Card
Name, title, email, phone #’s, web address and physical address
Font styles to use
Other font styles liked:
- Helvetica, Garamond, etc
Colors
Designer to choose only greyscale colors for use in the design.
Requirements
Must have
- Attached logo first or second options.
Nice to have
- Two sided card with logo on one side. Attached Logo/company name can be laid out any way that flows as long as it’s legible.name
Should not have
- No loud colors. ***Please do not include logo, I have removed the company design with a logo image.

```html
<!DOCTYPE html>
<html lang="en">
<head>
<meta charset="utf-8">
<title>Quarrystone Development Group, LLC — Business Card</title>
<link rel="stylesheet" href="https://fonts.googleapis.com/css2?family=EB+Garamond:wght@400;500&display=swap">
<style>
  :root {
    --backdrop: #d9dadc;
    --card: #4b5366;
    --card-deep: #3f4657;
    --ink: #ffffff;
    --ink-soft: #e4e6ec;
    --rule: rgba(255,255,255,0.75);
    --shadow: rgba(0,0,0,0.25);
  }
  * { box-sizing: border-box; margin: 0; padding: 0; }
  html, body { width: 1200px; height: 800px; overflow: hidden; }
  body {
    background: var(--backdrop);
    font-family: "EB Garamond", Garamond, serif;
    color: var(--ink);
    position: relative;
  }
  .card {
    position: absolute;
    width: 520px;
    height: 297px;
    background: var(--card);
    box-shadow: 0 10px 24px var(--shadow);
    overflow: hidden;
  }
  .card--front { left: 70px; top: 110px; }
  .card--back { left: 610px; top: 393px; }

  /* Front */
  .wordmark {
    position: absolute;
    left: 0; right: 0; top: 44px;
    text-align: center;
    color: var(--ink);
    font-weight: 400;
  }
  .wordmark__name { font-size: 38px; letter-spacing: 3px; line-height: 1; }
  .wordmark__sub { font-size: 12px; letter-spacing: 3px; margin-top: 6px; }
  .divider {
    position: absolute;
    left: 34px; right: 34px; top: 150px;
    height: 1px; background: var(--rule);
  }
  .person {
    position: absolute;
    left: 34px; top: 170px;
    width: 190px;
  }
  .person__name { font-size: 19px; letter-spacing: 1.5px; line-height: 1.1; }
  .person__title { font-size: 13px; color: var(--ink-soft); margin-top: 2px; }
  .person__rule { height: 1px; background: var(--rule); margin: 8px 0 7px; width: 170px; }
  .contact-list { list-style: none; font-size: 13px; line-height: 1.45; }
  .contact-list li { display: flex; align-items: center; gap: 8px; }
  .contact-list svg { width: 10px; height: 10px; fill: var(--ink); flex: none; }
  .address {
    position: absolute;
    right: 34px; top: 170px;
    text-align: right;
    font-size: 13px;
    line-height: 1.45;
  }

  /* Back */
  .back-pattern {
    position: absolute; inset: 0;
    background: linear-gradient(120deg, #5a6275 0%, var(--card) 45%, var(--card-deep) 100%);
  }
  .back-mark {
    position: absolute;
    right: 40px; bottom: 44px;
    font-size: 14px;
    letter-spacing: 2px;
    color: var(--ink);
  }
</style>
</head>
<body>

  <section class="card card--front" aria-label="Card front">
    <div class="wordmark">
      <div class="wordmark__name">QUARRYSTONE</div>
      <div class="wordmark__sub">DEVELOPMENT GROUP, LLC</div>
    </div>
    <div class="divider"></div>

    <div class="person">
      <div class="person__name">DANIEL HARROW</div>
      <div class="person__title">President</div>
      <div class="person__rule"></div>
      <ul class="contact-list">
        <li>
          <svg viewBox="0 0 10 10" aria-hidden="true"><path d="M2 0.5 L3.6 2.6 L2.8 3.6 Q4 6 6.4 7.2 L7.4 6.4 L9.5 8 L8.3 9.5 Q3.5 9 0.5 1.7 Z"/></svg>
          555-214-7380
        </li>
        <li>
          <svg viewBox="0 0 10 10" aria-hidden="true"><rect x="1" y="3" width="8" height="5" rx="0.5"/><rect x="2.5" y="0.8" width="5" height="2.6"/></svg>
          555-326-1947
        </li>
        <li>
          <svg viewBox="0 0 10 10" aria-hidden="true"><path d="M0.5 2 H9.5 V8.5 H0.5 Z M1.2 2.6 L5 5.6 L8.8 2.6 Z" fill-rule="evenodd"/></svg>
          info@quarrystone.com
        </li>
      </ul>
    </div>

    <div class="address">
      2140 Larkspur Court<br>
      Kenai Falls, Alaska 99621<br>
      www.quarrystone.com
    </div>
  </section>

  <section class="card card--back" aria-label="Card back">
    <div class="back-pattern" role="img" aria-label="Tonal repeating pattern of the company mark across the card back"></div>
    <div class="back-mark">QUARRYSTONE</div>
  </section>

</body>
</html>
```